Fenwick Grading LTD - website for irrigation & Landscape Lighting & Buried service wire

Looking for a website to help promote my business with Irrigation (installation, service, etc) and buried service wire/drainage solutions.

Commercial/Residential

Landscape lighting.

I’ll get photos in the trucks and trailers to upload as well maybe the machine as well.

Target Market(s)

Homeowners who want green grass and beautiful gardens. Beautiful landscape lighting

Industry/Entity Type

Irrigation systems and landscape lighting and buried service wire to homes and offering Drainage soltions.

Coding

Coded - Design and coding required

Number of Pages Required

4 page

Colors
F0912C
F2A743
F7CA91
FBE8D2
FDF5EE

Requirements
Must have
• was hoping to link up my email on fenwickgrading@mailbox-example.net with the website if possible.
Nice to have
• Page for Irrigation, page for landscape lighting, page buried service wire & drainage soltions.

```html
<!DOCTYPE html>
<html lang="en">
<head>
<meta charset="UTF-8">
<title>Fenwick Grading LTD — Irrigation, Landscape Lighting, Buried Wire & Drainage</title>
<link href="https://fonts.googleapis.com/css2?family=Montserrat:wght@400;500;600&family=Oswald:wght@500&display=swap" rel="stylesheet">
<style>
:root{
  --orange:#F0912C;
  --orange-2:#F2A743;
  --orange-3:#F7CA91;
  --cream:#FBE8D2;
  --ivory:#FDF5EE;
  --ink:#1a1a1a;
  --body:#5a5a5a;
  --white:#ffffff;
  --night:#1d231d;
}
*{margin:0;padding:0;box-sizing:border-box}
html,body{width:1200px;height:2965px;overflow:hidden;background:var(--white);font-family:'Montserrat',sans-serif;color:var(--ink)}
.page{position:relative;width:1200px;height:2965px;overflow:hidden}
.abs{position:absolute}

/* hero */
.hero{position:absolute;left:0;top:0;width:1200px;height:600px}
.hero-photo{position:absolute;inset:0;background:
  radial-gradient(ellipse 260px 120px at 330px 500px, rgba(240,170,80,.55), transparent 70%),
  radial-gradient(ellipse 300px 140px at 880px 420px, rgba(200,170,70,.45), transparent 70%),
  radial-gradient(ellipse 200px 90px at 500px 260px, rgba(230,190,120,.30), transparent 70%),
  linear-gradient(180deg,#17222a 0%,#26322a 35%,#4a4322 70%,#3a3218 100%)}
.hero-shade{position:absolute;inset:0;background:rgba(0,0,0,.22)}
.brand{position:absolute;left:141px;top:30px;display:flex;align-items:center;gap:10px}
.brand-mark{width:14px;height:14px;background:var(--orange)}
.brand-name{color:var(--white);font-weight:600;font-size:17px;line-height:1.2;letter-spacing:.5px;text-transform:uppercase}
.nav{position:absolute;top:25px;right:139px;display:flex;align-items:center;gap:29px}
.nav a{color:var(--white);font-size:12px;font-weight:500;text-decoration:none;white-space:nowrap}
.btn{display:inline-flex;align-items:center;justify-content:center;background:var(--orange);color:var(--white);font-size:12px;font-weight:500;text-decoration:none;border-radius:3px}
.nav .btn{width:106px;height:38px;margin-left:-12px}
.hero-title{position:absolute;left:0;top:228px;width:1200px;text-align:center;font-family:'Oswald',sans-serif;font-weight:500;font-size:37px;line-height:49px;color:var(--white)}
.hero-text{position:absolute;left:0;top:334px;width:1200px;text-align:center;color:var(--white);font-size:13px;line-height:23px}
.hero .btn.cta{position:absolute;left:540px;top:395px;width:105px;height:38px}

/* services */
.service{position:absolute;left:0;width:1200px;height:375px}
.blob{position:absolute;width:390px;height:380px}
.svc-copy{position:absolute;width:415px}
.svc-title{font-size:25px;font-weight:500;color:var(--ink);white-space:nowrap}
.svc-title span,.section-title span{color:var(--orange)}
.svc-lead{margin-top:24px;border-left:1.5px solid var(--orange);padding-left:12px;padding-right:20px;font-size:13px;font-weight:500;line-height:23px}
.svc-text{margin-top:14px;font-size:13px;line-height:22.6px;color:var(--body)}
.pill{display:inline-flex;align-items:center;justify-content:center;margin-top:28px;width:123px;height:35px;border-radius:18px;background:var(--orange);color:var(--white);font-size:12px;font-weight:500;letter-spacing:.8px;text-decoration:none}

/* testimonials */
.section-title{position:absolute;left:0;width:1200px;text-align:center;font-size:25px;font-weight:500}
.section-sub{position:absolute;left:0;width:1200px;text-align:center;font-size:13px;font-weight:500}
.quote{position:absolute;left:141px;top:2292px;width:480px;font-size:13px;line-height:22.6px;color:var(--ink)}
.quote-name{position:absolute;left:141px;top:2426px;font-size:15px;font-weight:500;color:var(--orange)}
.avatar{position:absolute;border-radius:50%}

/* footer */
.footer{position:absolute;left:0;top:2650px;width:1200px;height:315px}
.footer-photo{position:absolute;inset:0;background:
  radial-gradient(ellipse 320px 120px at 700px 260px, rgba(120,90,40,.35), transparent 70%),
  linear-gradient(180deg,var(--night) 0%,#252a20 60%,#1a1d17 100%)}
.footer .brand{left:141px;top:84px}
.footer .brand-name{font-size:20px}
.f-col{position:absolute;top:62px}
.f-col h4{font-size:15px;font-weight:500;color:var(--orange);margin-bottom:12px}
.f-col a,.f-col p{display:block;color:var(--white);font-size:12.5px;text-decoration:none;line-height:27.6px;white-space:nowrap}
.contact-row{display:flex;gap:12px;align-items:flex-start;color:var(--white);font-size:12.5px;line-height:20px;margin-bottom:14px}
.contact-row svg{flex:none;margin-top:2px}
.contact-row .mail{font-size:11px;white-space:nowrap}
.f-rule{position:absolute;left:141px;top:257px;width:918px;height:1px;background:rgba(255,255,255,.25)}
.copyright{position:absolute;left:141px;top:278px;color:var(--white);font-size:12.5px}
.social{position:absolute;top:273px;left:926px;display:flex;gap:11px}
.social span{width:24px;height:24px;border-radius:50%;background:var(--orange)}
</style>
</head>
<body>
<div class="page">

  <header class="hero">
    <div class="hero-photo" role="img" aria-label="Night garden with a wooden footbridge among trees lit by warm landscape lights"></div>
    <div class="hero-shade"></div>
    <div class="brand"><span class="brand-mark"></span><span class="brand-name">Fenwick Grading<br>LTD</span></div>
    <nav class="nav">
      <a href="#">Home</a>
      <a href="#">Irrigation</a>
      <a href="#">Landscape Lighting</a>
      <a href="#">Buried Wire &amp; Drainage</a>
      <a class="btn" href="#">Contact Us</a>
    </nav>
    <h1 class="hero-title">Transform Your Outdoor Space With Our Expert<br>Irrigation And Lighting Solutions</h1>
    <p class="hero-text">Get the perfect blend of form and function with our state-of-the-art irrigation systems and landscape lighting.<br>Trust our experienced team to deliver buried service wire and drainage solutions for your property</p>
    <a class="btn cta" href="#">Contact Us</a>
  </header>

  <!-- Irrigation -->
  <section class="service" style="top:690px">
    <svg class="blob" style="left:150px;top:0" viewBox="0 0 390 380">
      <defs><linearGradient id="g-irr" x1="0" y1="0" x2="0" y2="1"><stop offset="0" stop-color="#cdd6de"/><stop offset=".5" stop-color="#a7b1b0"/><stop offset=".75" stop-color="#6f8466"/><stop offset="1" stop-color="#3f5a36"/></linearGradient></defs>
      <path d="M200 4C268 0 348 70 372 150C392 220 338 270 250 304C170 334 90 376 40 370C2 365 0 300 24 238C54 160 112 8 200 4Z" fill="none" stroke="var(--orange)" stroke-width="1.5"/>
      <path role="img" aria-label="Sprinkler head spraying water over a misty field" d="M188 8C256 6 326 72 344 148C360 212 306 254 226 286C150 316 74 356 36 348C4 342 2 286 24 228C52 156 104 12 188 8Z" fill="url(#g-irr)"/>
    </svg>
    <div class="svc-copy" style="left:639px;top:44px">
      <h2 class="svc-title">Irrigation <span>Systems</span></h2>
      <p class="svc-lead">Efficient and Effective Watering Solutions for Your Lawn and Garden</p>
      <p class="svc-text">Our irrigation systems are designed to provide your lawn and garden with the right amount of water, without wasting a single drop. With our expert installation and service, you can rest assured that your plants will receive the nourishment they need to thrive.</p>
      <a class="pill" href="#">LEARN MORE</a>
    </div>
  </section>

  <!-- Landscape Lighting -->
  <section class="service" style="top:1168px">
    <div class="svc-copy" style="left:141px;top:44px">
      <h2 class="svc-title">Landscape <span>Lighting</span></h2>
      <p class="svc-lead">Enhance Your Outdoor Space with Beautiful and Functional Lighting Solutions</p>
      <p class="svc-text">Our landscape lighting solutions are designed to enhance the beauty and functionality of your outdoor space. From subtle pathway lighting to dramatic spotlights, we'll work with you to create a lighting plan that meets your needs and complements your landscape.</p>
      <a class="pill" href="#">LEARN MORE</a>
    </div>
    <svg class="blob" style="left:665px;top:0" viewBox="0 0 390 380">
      <defs><linearGradient id="g-light" x1="0" y1="0" x2="0" y2="1"><stop offset="0" stop-color="#3e5530"/><stop offset=".45" stop-color="#6f8f3a"/><stop offset=".7" stop-color="#8aa447"/><stop offset="1" stop-color="#3b3422"/></linearGradient></defs>
      <path d="M200 4C268 0 348 70 372 150C392 220 338 270 250 304C170 334 90 376 40 370C2 365 0 300 24 238C54 160 112 8 200 4Z" fill="none" stroke="var(--orange)" stroke-width="1.5"/>
      <path role="img" aria-label="Garden lawn at dusk with glowing bollard path lights and shrubs" d="M188 8C256 6 326 72 344 148C360 212 306 254 226 286C150 316 74 356 36 348C4 342 2 286 24 228C52 156 104 12 188 8Z" fill="url(#g-light)"/>
    </svg>
  </section>

  <!-- Buried Wire & Drainage -->
  <section class="service" style="top:1645px">
    <svg class="blob" style="left:150px;top:0" viewBox="0 0 390 380">
      <defs><linearGradient id="g-wire" x1="0" y1="0" x2="1" y2="1"><stop offset="0" stop-color="#b7a58c"/><stop offset=".5" stop-color="#6b5038"/><stop offset="1" stop-color="#2e2a24"/></linearGradient></defs>
      <path d="M200 4C268 0 348 70 372 150C392 220 338 270 250 304C170 334 90 376 40 370C2 365 0 300 24 238C54 160 112 8 200 4Z" fill="none" stroke="var(--orange)" stroke-width="1.5"/>
      <path role="img" aria-label="Open trench in a yard with conduit and drainage pipe being laid" d="M188 8C256 6 326 72 344 148C360 212 306 254 226 286C150 316 74 356 36 348C4 342 2 286 24 228C52 156 104 12 188 8Z" fill="url(#g-wire)"/>
    </svg>
    <div class="svc-copy" style="left:639px;top:68px">
      <h2 class="svc-title">Buried Wire <span>&amp; Drainage</span></h2>
      <p class="svc-lead">Buried Service Wire and Drainage Solutions for Your Property</p>
      <p class="svc-text">Our crew trenches and lays service wire to your home with precision and care. We also design drainage that moves water away from foundations and lawns, so your yard stays dry, level and ready for years of use.</p>
      <a class="pill" href="#">LEARN MORE</a>
    </div>
  </section>

  <!-- Testimonials -->
  <h2 class="section-title" style="top:2116px">What Our <span>Customers</span> Say</h2>
  <p class="section-sub" style="top:2165px">Hear from Our Satisfied Clients</p>
  <p class="quote">They maintain around 52 acres for us including several thousand sq ft or beds. Always answer thr phone and very prompt if we ever have an issue. Great guys all the way around! It is a long established fact that a reader will be distracted by the readable content of a page when looking at its layout.</p>
  <p class="quote-name">Marcus Delaney</p>
  <svg class="abs" style="left:141px;top:2501px" width="36" height="14" viewBox="0 0 36 14"><path d="M35 7H2M8 1L2 7l6 6" fill="none" stroke="var(--ink)" stroke-width="1.5"/></svg>
  <svg class="abs" style="left:232px;top:2501px" width="36" height="14" viewBox="0 0 36 14"><path d="M1 7h33M28 1l6 6-6 6" fill="none" stroke="var(--ink)" stroke-width="1.5"/></svg>

  <svg class="abs" style="left:708px;top:2222px" width="242" height="348" viewBox="0 0 242 348">
    <defs><linearGradient id="g-por" x1="0" y1="0" x2="0" y2="1"><stop offset="0" stop-color="#b9c4cc"/><stop offset=".5" stop-color="#8a8f95"/><stop offset="1" stop-color="#1f2530"/></linearGradient></defs>
    <path d="M120 4C185 4 238 55 238 118V228C238 292 190 344 126 344H122" fill="none" stroke="var(--orange)" stroke-width="1.5"/>
    <rect role="img" aria-label="Portrait of the featured customer" x="3" y="2" width="230" height="338" rx="115" fill="url(#g-por)"/>
  </svg>
  <div class="avatar" role="img" aria-label="Customer portrait" style="left:946px;top:2174px;width:111px;height:111px;background:linear-gradient(160deg,#d8d6d2,#8a2a2e)"></div>
  <div class="avatar" role="img" aria-label="Customer portrait" style="left:592px;top:2444px;width:80px;height:80px;background:linear-gradient(160deg,#6d8f86,#2d3b3a)"></div>
  <div class="avatar" role="img" aria-label="Customer portrait" style="left:966px;top:2455px;width:70px;height:70px;background:linear-gradient(160deg,#b7c2c9,#2c2a28)"></div>

  <!-- Footer -->
  <footer class="footer">
    <div class="footer-photo" role="img" aria-label="Dimly lit garden at night"></div>
    <div class="brand"><span class="brand-mark"></span><span class="brand-name">Fenwick Grading<br>LTD</span></div>
    <div class="f-col" style="left:459px">
      <h4>Quick Links</h4>
      <a href="#">Home</a><a href="#">Irrigation</a><a href="#">Landscape Lighting</a><a href="#">Buried Wire &amp; Drainage</a>
    </div>
    <div class="f-col" style="left:670px">
      <h4>Useful Links</h4>
      <a href="#">Contact</a><a href="#">Privacy Policy</a><a href="#">Terms of Service</a>
    </div>
    <div class="f-col" style="left:839px;width:262px">
      <h4>Contact Info</h4>
      <div class="contact-row"><svg width="16" height="18" viewBox="0 0 16 18"><path d="M8 1a6 6 0 0 0-6 6c0 4.5 6 10 6 10s6-5.5 6-10a6 6 0 0 0-6-6z" fill="none" stroke="var(--orange)" stroke-width="1.6"/><circle cx="8" cy="7" r="2.2" fill="var(--orange)"/></svg><span>Address Line 1, Address<br>Line 2, Address Line 3.</span></div>
      <div class="contact-row"><svg width="16" height="12" viewBox="0 0 16 12"><rect x="0" y="0" width="16" height="12" rx="1.5" fill="var(--orange)"/><path d="M1 1.5l7 5 7-5" fill="none" stroke="#252a20" stroke-width="1.4"/></svg><span class="mail">fenwickgrading@mailbox-example.net</span></div>
      <div class="contact-row"><svg width="16" height="16" viewBox="0 0 16 16"><path d="M3.5 1l2.5 3-1.6 2c.9 2 2.6 3.7 4.6 4.6l2-1.6 3 2.5-1.5 2.5C8 14 2 8 1 2.5z" fill="var(--orange)"/></svg><span>123-456-7890</span></div>
    </div>
    <div class="f-rule"></div>
    <p class="copyright">© 2024 Fenwick Grading. All rights reserved.</p>
    <div class="social" aria-label="Social media links"><span></span><span></span><span></span><span></span></div>
  </footer>

</div>
</body>
</html>
```